Request for Business Card Design

Hi. My name is Marlene, I am looking for a new business card design for my company, Quarrow Signal Instruments, LLC. I really like the design you did for Tarsel Venture and was hoping you could do something similar using our full logo and our mark. I am also open to any raised texture design using our mark. I have attached our full logo, which would need to be somewhere on the card, as well as the mark in both outline and full form, as well as our brand colors / guide. The card does not have to be white, as long as our logo and mark appear. I actually like darker colored business cards more, but am open to all options. If you are interested in working with me, please let me know. We would also take the business card design into letterhead design if you can do that.

```html
<!DOCTYPE html>
<html lang="en">
<head>
<meta charset="utf-8">
<title>Quarrow Signal Instruments – Business Card</title>
<link href="https://fonts.googleapis.com/css2?family=Open+Sans:wght@400;600;700;800&display=swap" rel="stylesheet">
<style>
  :root {
    --stage: #242424;
    --card-dark: #3b3c3f;
    --card-shade: #313235;
    --card-deep: #2a2b2e;
    --brand-blue: #1a9bc9;
    --brand-blue-deep: #137fa6;
    --brand-blue-light: #3fb3dc;
    --ink-light: #ffffff;
    --ink-muted: #dfe3e6;
  }
  * { box-sizing: border-box; margin: 0; padding: 0; }
  html, body {
    width: 1200px; height: 780px; overflow: hidden;
    background: var(--stage);
    font-family: "Open Sans", Arial, sans-serif;
  }
  .canvas {
    position: relative; width: 1200px; height: 780px;
    display: flex; justify-content: center; align-items: center; gap: 110px;
  }
  .card {
    position: relative; width: 360px; height: 620px;
    border-radius: 26px; overflow: hidden;
  }

  /* Front side */
  .card-front {
    background: var(--brand-blue);
  }
  .front-texture {
    position: absolute; inset: 0;
    background: linear-gradient(160deg, var(--brand-blue-light) 0%, var(--brand-blue) 45%, var(--brand-blue-deep) 100%);
  }
  .front-brand {
    position: absolute; top: 34px; right: 30px;
    display: flex; align-items: center; gap: 10px;
  }
  .brand-dot {
    width: 22px; height: 22px; border-radius: 50%;
    background: var(--ink-light);
  }
  .front-brand .brand-name {
    font-weight: 700; font-size: 13px; letter-spacing: 1.5px;
    color: var(--ink-light); text-transform: uppercase;
  }

  /* Back side */
  .card-back { background: var(--card-dark); }
  .back-curves { position: absolute; inset: 0; }
  .back-brand {
    position: absolute; top: 56px; left: 0; right: 0;
    display: flex; justify-content: center; align-items: center; gap: 12px;
  }
  .back-brand .brand-dot { width: 34px; height: 34px; background: var(--brand-blue); }
  .back-brand .brand-name {
    font-weight: 700; font-size: 15px; letter-spacing: 1.2px;
    color: var(--ink-light); text-transform: uppercase; line-height: 1.25;
  }
  .person {
    position: absolute; top: 222px; left: 0; right: 0; text-align: center;
  }
  .person-name {
    font-weight: 800; font-size: 46px; color: var(--brand-blue); line-height: 1;
  }
  .person-role {
    font-weight: 600; font-size: 17px; color: var(--ink-light); margin-top: 4px;
  }
  .contact-map { position: absolute; left: 0; top: 0; }
  .contact-list {
    position: absolute; top: 336px; left: 0; right: 0;
    list-style: none; text-align: center;
    color: var(--ink-light); font-size: 15px; line-height: 23px;
  }
  .contact-list .web-line { margin-top: 2px; }
  .address {
    position: absolute; top: 508px; left: 0; right: 0; text-align: center;
    color: var(--ink-light); font-size: 16px; line-height: 23px;
  }
  .address svg { display: block; margin: 0 auto 8px; }
</style>
</head>
<body>
<main class="canvas">

  <section class="card card-front" aria-label="Card front">
    <div class="front-texture" role="img" aria-label="Raised repeating pattern of the company mark on brand blue"></div>
    <div class="front-brand">
      <span class="brand-name">Quarrow Signal Instruments</span>
      <span class="brand-dot"></span>
    </div>
  </section>

  <section class="card card-back" aria-label="Card back">
    <svg class="back-curves" width="360" height="620" viewBox="0 0 360 620" aria-hidden="true">
      <path d="M0 430 C 90 520, 270 520, 360 400 L360 620 L0 620 Z" fill="var(--card-shade)"/>
      <path d="M0 500 C 120 470, 260 520, 360 470 L360 620 L0 620 Z" fill="var(--card-deep)" opacity="0.55"/>
      <path d="M0 430 C 90 520, 270 520, 360 400" fill="none" stroke="#26272a" stroke-width="3" opacity="0.6"/>
    </svg>

    <div class="back-brand">
      <span class="brand-dot"></span>
      <span class="brand-name">Quarrow<br>Signal Instruments</span>
    </div>

    <div class="person">
      <p class="person-name">Marlene</p>
      <p class="person-role">Director</p>
    </div>

    <svg class="contact-map" width="360" height="620" viewBox="0 0 360 620" aria-hidden="true">
      <g fill="none" stroke="var(--brand-blue)" stroke-width="1.6">
        <polyline points="117,304 22,304 22,430 44,430"/>
        <polyline points="243,304 338,304 338,430 316,430"/>
        <polyline points="163,316 163,326 64,326 64,346 80,346"/>
        <polyline points="197,316 197,326 296,326 296,346 280,346"/>
      </g>
      <g fill="var(--brand-blue)">
        <path d="M44 425 L52 430 L44 435 Z"/>
        <path d="M316 425 L308 430 L316 435 Z"/>
        <path d="M80 341 L88 346 L80 351 Z"/>
        <path d="M280 341 L272 346 L280 351 Z"/>
        <circle cx="129" cy="304" r="13"/>
        <circle cx="163" cy="304" r="13"/>
        <circle cx="197" cy="304" r="13"/>
        <circle cx="231" cy="304" r="13"/>
      </g>
      <g fill="none" stroke="#fff" stroke-width="1.4" stroke-linecap="round" stroke-linejoin="round">
        <rect x="122" y="299" width="14" height="10" rx="1"/>
        <polyline points="122,300 129,305 136,300"/>
        <path d="M158 298 q-2 4 2 9 q4 4 8 2 l-2-3 -2 1 q-3-2-4-5 l1-2 z"/>
        <rect x="191" y="300" width="12" height="9" rx="1"/>
        <line x1="194" y1="304" x2="200" y2="304"/>
        <circle cx="231" cy="304" r="6"/>
        <line x1="225" y1="304" x2="237" y2="304"/>
        <ellipse cx="231" cy="304" rx="2.6" ry="6"/>
      </g>
    </svg>

    <ul class="contact-list">
      <li>+001 555 270 3318</li>
      <li>+001 555 270 4402</li>
      <li>info@quarrowsignal.com</li>
      <li class="web-line">www.quarrowsignal.com</li>
    </ul>

    <div class="address">
      <svg width="26" height="26" viewBox="0 0 26 26" aria-hidden="true">
        <circle cx="13" cy="13" r="13" fill="var(--brand-blue)"/>
        <path d="M13 6 a4.5 4.5 0 0 1 4.5 4.5 c0 3.2-4.5 8-4.5 8 s-4.5-4.8-4.5-8 A4.5 4.5 0 0 1 13 6 z" fill="none" stroke="#fff" stroke-width="1.4"/>
        <circle cx="13" cy="10.5" r="1.6" fill="#fff"/>
      </svg>
      <p>1180 Harrow Park Drive &bull;</p>
      <p>Elmstead, CO 80612</p>
    </div>
  </section>

</main>
</body>
</html>
```